Pinecrest Harbor Foundation Web Design

The design we need is for a WordPress blog that will be our content platform. We are a registered 501(c)3 non-profit that focuses on financially supporting the treatment of cancer patients that have been told they have no hope and there is nothing the conventional medical system can do for them. Through this wesbite we want to both rasie awareness about the treatment options plus, raise funds for treating patients. The two primary target audiences of the site are...

1. Terminally ill patients and their families to let them know that there is an option other then hospice and that we are hear to support that option.

2. People looking to help donate to a worthwhile cause that resonates with them.

The website is https://pinecrestharborfoundation.org/

See attached logo designs!!!

Target Market(s)

Cancer patients and their families

Industry/Entity Type

Foundation

Font styles to use
Sans Serif

Colors
ffffff
fbed22

Requirements
Must have
• I like this look of this site. It is clean, simple, helpful, soft. I like the flow of the pages.
• http://www.meadowsforcalm.org/
• I like the design and flow but NOT the color or boldness
• https://tvbn-youth.org/
• I like this style for a donation page.
• https://www.tumorstudyhub.org/we-are-tsh/join-the-cause/donations/one-time-donation
• with the addition of a Would you like your employer to match? button.
Nice to have
• White black and gold - but soft
• Even possibly grayscale like the site I like.

```html
<!DOCTYPE html>
<html lang="en">
<head>
<meta charset="utf-8">
<title>Pinecrest Harbor Foundation</title>
<link rel="stylesheet" href="https://fonts.googleapis.com/css2?family=Lato:ital,wght@0,400;0,700;0,900;1,400&display=swap">
<style>
:root{
  --teal:#17aeae;
  --teal-light:#35cccc;
  --orange:#f46b12;
  --ink:#222;
  --text:#333;
  --grey-band:#e9e9e9;
  --hero-bg:#dde3e8;
  --footer-bar:#333;
}
*{margin:0;padding:0;box-sizing:border-box}
html,body{width:1200px;height:2546px;overflow:hidden;background:#fff}
body{font-family:'Lato',sans-serif;color:var(--text);position:relative}
.abs{position:absolute}

/* header */
.brand{left:75px;top:20px;font-size:26px;font-weight:700;line-height:30px;text-transform:uppercase;color:var(--ink)}
.brand .top{color:var(--teal)}
.header-phone{left:754px;top:38px;font-size:22px;color:var(--ink);display:flex;align-items:center;gap:12px}
.donate{left:973px;top:30px;width:152px;height:48px;background:var(--orange);color:#fff;font-size:16px;font-weight:700;display:flex;align-items:center;justify-content:center;border-radius:2px}

/* nav */
.nav{left:0;top:100px;width:1200px;height:58px;background:linear-gradient(#35cfcf,#16a8a8)}
.nav ul{list-style:none;display:flex;position:absolute;left:75px;top:0;height:58px}
.nav li{height:58px;display:flex;align-items:center;color:#fff;font-size:14px;font-weight:700;text-transform:uppercase;padding:0 25px}
.nav li.active{background:var(--orange)}
.nav li+li{margin-left:14px}

/* hero */
.hero{left:0;top:158px;width:1200px;height:520px;background:var(--hero-bg)}
.hero-photo{left:560px;top:0;width:640px;height:520px;background:linear-gradient(90deg,#dde3e8 0%,#c9cfd6 30%,#b5a593 70%,#c7bcae 100%)}
.hero-title{left:75px;top:110px;font-size:38px;font-weight:700;color:var(--orange);line-height:46px;text-transform:uppercase}
.hero-text{left:75px;top:212px;width:520px;font-size:16px;line-height:26px;color:var(--ink)}
.btn-teal{background:var(--teal);color:#fff;font-weight:700;font-size:14px;text-transform:uppercase;display:flex;align-items:center;justify-content:center}
.hero-btn{left:75px;top:322px;width:150px;height:43px}
.dots{left:75px;top:460px;display:flex;gap:5px}
.dots span{width:10px;height:10px;background:#888;border-radius:2px}
.dots span:first-child{background:#222}

/* welcome */
.section-title{width:1200px;left:0;text-align:center;font-size:36px;font-weight:700;color:var(--teal);text-transform:uppercase}
.welcome-title{top:720px}
.welcome-text{left:110px;top:786px;width:980px;text-align:center;font-size:14px;line-height:26px;color:var(--ink)}

/* what we do */
.wwd{left:46px;top:943px;width:1154px;height:409px;background:var(--grey-band)}
.wwd-title{left:113px;top:1125px;font-size:38px;font-weight:700;color:#fff;text-transform:uppercase}
.service{font-size:21px;line-height:28px;color:var(--orange);text-transform:uppercase}

/* blog */
.blog-title{top:1395px}
.post-img{width:209px;height:180px}
.post-h{font-size:17px;font-weight:700;color:var(--orange);text-transform:uppercase}
.post-p{width:290px;font-size:14px;line-height:24px;color:var(--ink)}
.post-more{font-size:13px;font-style:italic;color:var(--teal)}

/* testimonials */
.testi{left:0;top:1720px;width:1200px;height:408px;background:var(--grey-band)}
.testi-text{left:75px;top:1832px;width:600px;font-size:13.5px;line-height:26px;font-style:italic;color:var(--ink)}
.testi-title{left:826px;top:1900px;font-size:38px;font-weight:700;color:#fff;text-transform:uppercase}
.avatar{left:75px;top:1994px;width:84px;height:84px;border-radius:50%;background:radial-gradient(#f0d7bf,#d9b48e)}
.name-h{left:181px;top:2017px;font-size:14px;font-weight:700;color:var(--orange);text-transform:uppercase}
.name-loc{left:181px;top:2039px;font-size:13px;font-style:italic;color:var(--ink)}

/* footer */
.fcol{top:2180px;font-size:14px;line-height:28.5px;color:var(--ink)}
.fcol h4{font-size:14px;font-weight:700;color:var(--orange);text-transform:uppercase;line-height:20px;margin-bottom:6px}
.fcol .org{color:var(--teal);font-weight:700}
.fcol .ic{display:inline-flex;width:28px;align-items:center}
.reg{font-size:11px;font-weight:700;text-transform:uppercase;line-height:18px}
.email-field{width:240px;height:42px;background:#eee;border:1px solid #ddd;font-size:13px;color:#555;padding:0 14px;display:flex;align-items:center;margin-top:14px;line-height:1}
.signup{width:89px;height:38px;margin:12px 0 0 151px}
.bottom-bar{left:0;top:2468px;width:1200px;height:78px;background:var(--footer-bar)}
.copyright{left:75px;top:2500px;font-size:11px;color:#ccc}
.socials{left:910px;top:2495px;display:flex;gap:20px}
.socials span{width:24px;height:24px;border-radius:50%;background:#bbb}
</style>
</head>
<body>

<header>
  <div class="abs brand"><div class="top">Pinecrest Harbor</div><div>Foundation</div></div>
  <div class="abs header-phone">
    <svg width="16" height="16" viewBox="0 0 24 24"><path fill="#17aeae" d="M6.6 10.8a15 15 0 0 0 6.6 6.6l2.2-2.2c.3-.3.7-.4 1-.2 1.1.4 2.3.6 3.6.6.6 0 1 .4 1 1V20c0 .6-.4 1-1 1A17 17 0 0 1 3 4c0-.6.4-1 1-1h3.5c.6 0 1 .4 1 1 0 1.3.2 2.5.6 3.6.1.3 0 .7-.2 1z"/></svg>
    1-800-555-0142
  </div>
  <div class="abs donate">DONATE</div>
</header>

<nav class="abs nav">
  <ul>
    <li class="active">Home</li><li>About Us</li><li>Services</li><li>Blog</li><li>Testimonials</li><li>News</li><li>Careers</li><li>Contact Us</li>
  </ul>
</nav>

<section class="abs hero">
  <div class="abs hero-photo" role="img" aria-label="Photo of a doctor talking with a smiling patient wearing a headscarf"></div>
  <h1 class="abs hero-title">Pinecrest Harbor<br>Foundation</h1>
  <p class="abs hero-text">Aliquam molestie, mi et imperdiet euismod, dui purus auctor tellus, et interdum lacus lectus et ante. Sed accumsan sollicitudin sapien, sit amet adipiscing turpis gravida ac.</p>
  <div class="abs btn-teal hero-btn">Read More</div>
  <div class="abs dots"><span></span><span></span><span></span><span></span></div>
</section>

<h2 class="abs section-title welcome-title">Welcome to Our Website</h2>
<p class="abs welcome-text">Aliquam molestie, mi et imperdiet euismod, dui purus auctor tellus, et interdum lacus lectus et ante. Sed accumsan sollicitudin sapien, sit amet adipiscing turpis gravida ac. In congue, neque ac lobortis volutpat, libero mauris varius mi, vitae suscipit ipsum ligula vitae risus. Duis aliquam nibh a dui iaculis viverra id a velit. Vivamus egestas risus in magna varius commodo. Sed semper viverra egestas. Etiam pretium porttitor lectus, vel ornare neque porta volutpat.</p>

<section class="abs wwd">
  <svg class="abs" style="left:0;top:0" width="1154" height="409" viewBox="0 0 1154 409">
    <defs><linearGradient id="wwdPhoto" x1="0" x2="1"><stop offset="0" stop-color="#6b6865"/><stop offset="1" stop-color="#4e4c4a"/></linearGradient></defs>
    <polygon points="0,0 602,0 416,205 602,409 0,409" fill="url(#wwdPhoto)" role="img" aria-label="Photo of a doctor with a patient in a hospital room"/>
    <polyline points="602,0 416,205 602,409" fill="none" stroke="#17aeae" stroke-width="3"/>
    <g fill="#e9e9e9" stroke="#17aeae" stroke-width="3">
      <circle cx="499" cy="97" r="40"/><circle cx="416" cy="205" r="40"/><circle cx="499" cy="314" r="40"/>
    </g>
    <path d="M499 80c-6 0-9 4-9 9 0 4 3 9 6 13l-8 11 5 3 7-9 7 9 5-3-8-11c3-4 6-9 6-13 0-5-3-9-9-9zm0 5c3 0 4 2 4 4 0 3-2 6-4 9-2-3-4-6-4-9 0-2 1-4 4-4z" fill="#222"/>
    <g fill="#222"><rect x="400" y="193" width="32" height="24" rx="3"/><rect x="410" y="187" width="12" height="7" rx="1" fill="none" stroke="#222" stroke-width="3"/></g>
    <path d="M414 205h4v-4h4v4h4v4h-4v4h-4v-4h-4z" fill="#e9e9e9" transform="translate(-4,-2)"/>
    <text x="499" y="326" text-anchor="middle" font-family="Lato,sans-serif" font-weight="700" font-size="34" fill="#222">$</text>
  </svg>
</section>
<h2 class="abs wwd-title">What We Do</h2>
<div class="abs service" style="left:613px;top:1013px">Treatment for people who are in final<br>stages of cancer</div>
<div class="abs service" style="left:537px;top:1113px">Raise awareness about the treatment<br>options plus</div>
<div class="abs service" style="left:613px;top:1215px">Raise funds for treating<br>patients</div>

<h2 class="abs section-title blog-title">Blog Posts</h2>
<article>
  <div class="abs post-img" style="left:75px;top:1480px;background:linear-gradient(135deg,#e07bb0,#c9a48e)" role="img" aria-label="Photo of many hands holding a pink ribbon"></div>
  <h3 class="abs post-h" style="left:307px;top:1476px">Aliquam Molestie</h3>
  <p class="abs post-p" style="left:307px;top:1505px">Sed accumsan sollicitudin sapien, sit amet adipiscing turpis gravida ac. In congue, neque ac lobortis volutpat, libero mauris varius mi, vitae suscipit ipsum ligula vitae risus.</p>
  <div class="abs post-more" style="left:307px;top:1642px">Continue Reading</div>
</article>
<article>
  <div class="abs post-img" style="left:614px;top:1480px;background:linear-gradient(135deg,#d8e2e6,#d9c2ae)" role="img" aria-label="Photo of a patient in a headscarf with a caring companion"></div>
  <h3 class="abs post-h" style="left:846px;top:1476px">Aliquam Molestie</h3>
  <p class="abs post-p" style="left:846px;top:1505px">Sed accumsan sollicitudin sapien, sit amet adipiscing turpis gravida ac. In congue, neque ac lobortis volutpat, libero mauris varius mi, vitae suscipit ipsum ligula vitae risus.</p>
  <div class="abs post-more" style="left:846px;top:1642px">Continue Reading</div>
</article>

<section class="abs testi">
  <svg class="abs" style="left:0;top:0" width="1200" height="408" viewBox="0 0 1200 408">
    <defs><linearGradient id="testiPhoto" x1="0" x2="1"><stop offset="0" stop-color="#b7a08c"/><stop offset="1" stop-color="#a08a7a"/></linearGradient></defs>
    <polygon points="598,0 1200,0 1200,408 598,408 790,204" fill="url(#testiPhoto)" role="img" aria-label="Photo of two smiling women, one wearing a headscarf"/>
    <polyline points="598,0 790,204 598,408" fill="none" stroke="#17aeae" stroke-width="3"/>
    <path d="M76 62h18v14c0 10-5 18-14 20l-2-5c5-2 7-6 7-11h-9zm24 0h18v14c0 10-5 18-14 20l-2-5c5-2 7-6 7-11h-9z" fill="#17aeae"/>
    <path d="M549 310l-8 8 8 8M565 310l8 8-8 8" fill="none" stroke="#555" stroke-width="2.5"/>
  </svg>
</section>
<p class="abs testi-text">Aliquam molestie, mi et imperdiet euismod, dui purus auctor tellus, et interdum lacus lectus et ante. Sed accumsan sollicitudin sapien, sit amet adipiscing turpis gravida ac. In congue, neque ac lobortis volutpat, libero mauris varius mi, vitae suscipit ipsum ligula vitae risus. Duis aliquam nibh a dui iaculis viverra id a velit. Vivamus egestas risus in magna varius commodo.<br>Sed semper viverra egestas..”</p>
<h2 class="abs testi-title">Testimonials</h2>
<div class="abs avatar" role="img" aria-label="Portrait photo of the person giving the testimonial"></div>
<div class="abs name-h">Name Heading</div>
<div class="abs name-loc">Location</div>

<footer>
  <div class="abs fcol" style="left:75px">
    <h4>Site Map</h4>
    Home<br>About Us<br>Services<br>Blog<br>Testimonials<br>News<br>Careers<br>Contact Us
  </div>
  <div class="abs fcol" style="left:328px">
    <h4>Contact Info</h4>
    <span class="org">Pinecrest Harbor Foundation</span><br>
    4127 Birchwood<br>Lane, Fairhaven, FH2 7LQ<br>
    <span class="ic"><svg width="13" height="13" viewBox="0 0 24 24"><path fill="#222" d="M6.6 10.8a15 15 0 0 0 6.6 6.6l2.2-2.2c.3-.3.7-.4 1-.2 1.1.4 2.3.6 3.6.6.6 0 1 .4 1 1V20c0 .6-.4 1-1 1A17 17 0 0 1 3 4c0-.6.4-1 1-1h3.5c.6 0 1 .4 1 1 0 1.3.2 2.5.6 3.6.1.3 0 .7-.2 1z"/></svg></span>1-800-555-0178<br>
    <span class="ic"><svg width="14" height="11" viewBox="0 0 14 11"><rect width="14" height="11" rx="1" fill="#222"/><path d="M1 1l6 5 6-5" fill="none" stroke="#fff" stroke-width="1.3"/></svg></span>hello@pinecrestharbor.org<br>
    <span class="ic"><svg width="11" height="15" viewBox="0 0 12 16"><path d="M6 0a6 6 0 0 0-6 6c0 4.5 6 10 6 10s6-5.5 6-10a6 6 0 0 0-6-6zm0 8.5A2.5 2.5 0 1 1 6 3.5a2.5 2.5 0 0 1 0 5z" fill="#222"/></svg></span>Map
    <h4 style="margin-top:16px">Registered Under</h4>
    <div class="reg">501(c)3 Non-Profit Organisation</div>
  </div>
  <div class="abs fcol" style="left:634px">
    <h4>Resources</h4>
    Vestibulum ante<br>Lpsum primis<br>Faucibus orci<br>Luctus et ultrices<br>Posuere cubilia
  </div>
  <div class="abs fcol" style="left:884px;line-height:22px">
    <h4>Email Subscribe</h4>
    Vestibulum ante ipsum primis in<br>faucibus orci luctus
    <div class="email-field">Enter Email Address</div>
    <div class="btn-teal signup">Sign Up</div>
  </div>
  <div class="abs bottom-bar"></div>
  <div class="abs copyright">Copyright © 2017. Company Name. All Right Reserved</div>
  <div class="abs socials"><span></span><span></span><span></span><span></span><span></span></div>
</footer>

</body>
</html>
```